Finding the Root: Reason in Clinical Choice-Crafting

I'd like a cover that looks like it would fit on the shelf next to "The Illness Mirage" by Corwin Talley, "The Close of Forgetting" by Hugh Marchetti, "Meal Mend" by Paul Grieve, "The Energy Restart Plan" by Oscar Pemberley or "The Gland Restart Plan" by the same or "The Cortex Restart Plan" by the same ... either text only (with some interesting fonts that make the title stand out, and the subtitle smaller) or a relevant image, though I'm not entirely sure what that would be since this is a book about big-picture medical decision making.
Author name is Dr Tessa Morrow, NMD
I'll eventually request an e-book, paperback, and audio cover from the winner...

Target Market(s)

practicing physicians

Industry/Entity Type

medicine

Requirements
Must have
• look similar to other books in the genre

```html
<!DOCTYPE html>
<html lang="en">
<head>
<meta charset="utf-8">
<title>Finding the Root: Reason in Clinical Choice-Crafting</title>
<link rel="stylesheet" href="https://fonts.googleapis.com/css2?family=Bebas+Neue&family=Playfair+Display:wght@600&family=Montserrat:wght@600;700&family=Oswald:wght@500&display=swap">
<style>
  :root {
    --backdrop: #9a9a9a;
    --paper: #fbfbfa;
    --navy: #0e1a2e;
    --green: #627535;
    --maze-light: #f6f6f5;
    --maze-shade: #e0e0de;
  }
  * { margin: 0; padding: 0; box-sizing: border-box; }
  html, body {
    width: 1200px; height: 1200px; overflow: hidden;
    background: var(--backdrop);
  }
  .cover {
    position: absolute; left: 200px; top: 0;
    width: 800px; height: 1200px;
    background: var(--paper);
    overflow: hidden;
  }
  .title-lead {
    position: absolute; top: 128px; left: 0; width: 100%;
    text-align: center;
    font-family: "Bebas Neue", "Oswald", sans-serif;
    font-size: 170px; line-height: 1;
    letter-spacing: 1px;
    color: var(--navy);
  }
  .title-key {
    position: absolute; top: 286px; left: 0; width: 100%;
    text-align: center;
    font-family: "Playfair Display", serif;
    font-weight: 600;
    font-size: 244px; line-height: 1;
    color: var(--green);
  }
  .subtitle-intro {
    position: absolute; top: 562px; left: 0; width: 100%;
    display: flex; align-items: center; justify-content: center; gap: 30px;
    font-family: "Montserrat", sans-serif; font-weight: 600;
    font-size: 26px; line-height: 1.1; letter-spacing: 0.3em;
    color: var(--navy);
  }
  .subtitle-intro .rule {
    display: block; width: 150px; height: 2px; background: var(--green);
  }
  .subtitle-key {
    position: absolute; top: 604px; left: 0; width: 100%;
    text-align: center;
    font-family: "Montserrat", sans-serif; font-weight: 700;
    font-size: 50px; line-height: 1.1; letter-spacing: 0.3em; padding-left: 0.3em;
    color: var(--green);
  }
  .subtitle-tail {
    position: absolute; top: 672px; left: 0; width: 100%;
    text-align: center;
    font-family: "Montserrat", sans-serif; font-weight: 600;
    font-size: 28px; line-height: 1.1; letter-spacing: 0.16em; padding-left: 0.16em;
    color: var(--navy);
    z-index: 2;
  }
  .maze-art {
    position: absolute; left: 211px; top: 724px;
    width: 376px; height: 288px; border-radius: 50%;
    background: radial-gradient(ellipse, var(--maze-light) 0%, var(--maze-shade) 60%, var(--paper) 74%);
  }
  .connectors { position: absolute; left: 0; top: 0; }
  .benefit {
    position: absolute;
    font-family: "Oswald", sans-serif; font-weight: 500;
    font-size: 19px; line-height: 1.3; letter-spacing: 0.12em;
    color: var(--navy); text-align: center;
  }
  .benefit-questions { left: 58px; top: 838px; }
  .benefit-decisions { left: 636px; top: 838px; }
  .benefit-outcomes { left: 340px; top: 1012px; width: 118px; }
  .author-band {
    position: absolute; left: 0; bottom: 0; width: 100%; height: 120px;
    background: var(--navy);
  }
  .author-band .band-rule {
    position: absolute; left: 83px; width: 634px; height: 2px; background: var(--green);
  }
  .author-band .band-rule.top { top: 17px; }
  .author-band .band-rule.bottom { top: 97px; }
  .author-name {
    position: absolute; top: 30px; left: 0; width: 100%;
    text-align: center;
    font-family: "Oswald", sans-serif; font-weight: 500;
    font-size: 44px; line-height: 1.3; letter-spacing: 0.16em; padding-left: 0.16em;
    color: #ffffff;
  }
</style>
</head>
<body>
  <main class="cover">
    <h1>
      <span class="title-lead">FINDING THE</span>
      <span class="title-key">ROOT</span>
    </h1>
    <p class="subtitle-intro"><span class="rule"></span>REASON IN<span class="rule"></span></p>
    <p class="subtitle-key">CLINICAL</p>
    <p class="subtitle-tail">CHOICE-CRAFTING</p>

    <div class="maze-art" role="img" aria-label="Embossed white circular maze with a path leading to a green medical cross at its centre"></div>

    <svg class="connectors" width="800" height="1080" aria-hidden="true">
      <g stroke="#627535" stroke-width="2" fill="#627535">
        <line x1="186" y1="867" x2="253" y2="867"/>
        <circle cx="186" cy="867" r="6"/>
        <line x1="533" y1="867" x2="621" y2="867"/>
        <circle cx="621" cy="867" r="6"/>
        <line x1="399" y1="926" x2="399" y2="1001"/>
        <circle cx="399" cy="1001" r="6"/>
      </g>
    </svg>

    <p class="benefit benefit-questions">BETTER<br>QUESTIONS</p>
    <p class="benefit benefit-decisions">BETTER<br>DECISIONS</p>
    <p class="benefit benefit-outcomes">BETTER<br>OUTCOMES</p>

    <footer class="author-band">
      <span class="band-rule top"></span>
      <p class="author-name">DR TESSA MORROW, NMD</p>
      <span class="band-rule bottom"></span>
    </footer>
  </main>
</body>
</html>
```